Larkspur Talent IT Recruiting firm needs a business card design for Recruiters, Sourcers, and Account

We need business cards that allow us to change all contact info, names, titles (Recruiter, Sourcer, Account Manager, Director, CEO, etc) per person since we have three offices, in three cities, Phoenix, Austin, and Las Vegas. We do recruiting and contractors for IT positions (Developers, Architects, Software Engineers, Security Engineers, Help Desk, DBAs, PMs, Scrum Masters, etc.) Our client companies are very diverse from Meridian 100 to silicone Valley type start-ups.

So, while we what hip, techie, and quirky, it still needs to be professional. Primary color we use is blue, with silver as a secondary color.

Target Market(s)

IT, Technology

Industry/Entity Type

Business

Contact Information for Business Card

Company name: Larkspur Talent, Inc.
Website: www.larkspurtalent.example
Logos for Careerloop, Blipster, and Myriada

Name, Title, Office Number, Cell Number, email

Font styles to use
Serif
Sans Serif

Colors
0455a3
d5d5d5

Requirements
Nice to have
• The grey I selected below is not necessary - but, would like silver included. I included a card design (File 3: LTI early trial example.jpg) that I had started on. It's very rough, and not quite what we're looking for, but what we did like is the logo, big, maybe a bit faded, off center, goes out of frame, etc. Still looking for other ideas - you are the pros! But, just an idea of a design element we liked.

```html
<!DOCTYPE html>
<html lang="en">
<head>
<meta charset="utf-8">
<title>Larkspur Talent – Business Card</title>
<link href="https://fonts.googleapis.com/css2?family=Cinzel:wght@400;500&family=Open+Sans:wght@400;700&display=swap" rel="stylesheet">
<style>
  :root {
    --brand-blue: #0455a3;
    --brand-blue-deep: #03478a;
    --silver: #d5d5d5;
    --silver-dark: #a9a9a9;
    --ink: #222222;
    --ink-soft: #3a3a3a;
    --paper: #ffffff;
    --backdrop: #ececec;
  }
  * { box-sizing: border-box; margin: 0; padding: 0; }
  html, body {
    width: 1200px; height: 904px; overflow: hidden;
    background: var(--backdrop);
  }
  .sheet {
    position: relative; width: 1200px; height: 904px;
    display: flex; flex-direction: column; align-items: center; justify-content: center;
    gap: 48px;
  }
  .card {
    position: relative; width: 660px; height: 377px;
    border-radius: 30px; overflow: hidden;
    box-shadow: 0 6px 18px rgba(0,0,0,0.18);
  }

  /* Back */
  .card--back { background: var(--brand-blue); color: var(--paper); }
  .back-mark {
    position: absolute; left: 50%; top: 44%; transform: translate(-50%, -50%);
    display: flex; flex-direction: column; align-items: center; gap: 18px;
  }
  .back-mark__dot { width: 150px; height: 150px; border-radius: 50%; background: var(--paper); }
  .back-mark__name {
    font-family: "Cinzel", serif; font-weight: 500; font-size: 30px;
    letter-spacing: 0.08em; text-transform: uppercase; color: var(--paper);
    white-space: nowrap;
  }
  .back-url {
    position: absolute; left: 0; right: 0; bottom: 34px; text-align: center;
    font-family: "Open Sans", sans-serif; font-size: 19px; letter-spacing: 0.14em;
    color: var(--paper);
  }

  /* Front */
  .card--front { background: var(--paper); color: var(--ink); }
  .brand {
    position: absolute; left: 44px; top: 40px;
    display: flex; align-items: center; gap: 12px;
  }
  .brand__dot { width: 40px; height: 40px; border-radius: 50%; background: var(--brand-blue); }
  .brand__name {
    font-family: "Cinzel", serif; font-weight: 500; font-size: 36px;
    letter-spacing: 0.04em; text-transform: uppercase; color: var(--ink);
    white-space: nowrap;
  }
  .tagline {
    position: absolute; left: 46px; top: 100px;
    font-family: "Cinzel", serif; font-size: 16px; letter-spacing: 0.12em;
    text-transform: uppercase; color: var(--ink-soft);
  }
  .divider {
    position: absolute; left: 0; right: 0; top: 150px; height: 2px;
    background: linear-gradient(90deg, rgba(213,213,213,0) 0%, var(--silver) 25%, var(--silver-dark) 60%, rgba(213,213,213,0.2) 100%);
  }
  .socials {
    position: absolute; left: 44px; top: 208px; list-style: none;
    font-family: "Open Sans", sans-serif; font-size: 15px; color: var(--ink-soft);
  }
  .socials li { display: flex; align-items: center; gap: 6px; margin-bottom: 8px; }
  .socials__dot { width: 13px; height: 13px; border-radius: 50%; background: var(--brand-blue); }
  .person {
    position: absolute; right: 44px; top: 196px; text-align: right;
    font-family: "Open Sans", sans-serif;
  }
  .person__name { font-weight: 700; font-size: 21px; color: var(--brand-blue); }
  .person__title { font-size: 16px; color: var(--ink-soft); margin-top: 4px; }
  .person-rule {
    position: absolute; right: 0; top: 256px; width: 330px; height: 2px;
    background: linear-gradient(90deg, rgba(169,169,169,0), var(--silver-dark));
  }
  .contact {
    position: absolute; right: 44px; bottom: 30px; list-style: none;
    font-family: "Open Sans", sans-serif; font-size: 16px; color: var(--ink);
  }
  .contact li { display: flex; align-items: center; justify-content: flex-end; gap: 8px; margin-top: 5px; white-space: nowrap; }
  .contact svg { width: 15px; height: 15px; flex: none; }
  .contact .icon-fill { fill: var(--brand-blue); }
  .contact .icon-line { fill: none; stroke: var(--brand-blue); }
  .card--front::after {
    content: ""; position: absolute; left: 0; right: 0; bottom: 0; height: 5px;
    background: var(--brand-blue-deep);
  }
</style>
</head>
<body>
<main class="sheet">

  <section class="card card--back" aria-label="Card back">
    <div class="back-mark">
      <span class="back-mark__dot"></span>
      <span class="back-mark__name">Larkspur Talent</span>
    </div>
    <p class="back-url">www.larkspurtalent.example</p>
  </section>

  <section class="card card--front" aria-label="Card front">
    <div class="brand">
      <span class="brand__dot"></span>
      <span class="brand__name">Larkspur Talent</span>
    </div>
    <p class="tagline">Talent That Delivers</p>
    <div class="divider"></div>

    <ul class="socials">
      <li><span class="socials__dot"></span>@MarenHollowayLT</li>
      <li><span class="socials__dot"></span>@MarenHollowayLT</li>
    </ul>

    <div class="person">
      <p class="person__name">Maren Holloway</p>
      <p class="person__title">First Touch Embassador</p>
    </div>
    <div class="person-rule"></div>

    <ul class="contact">
      <li>
        <svg viewBox="0 0 16 16" aria-hidden="true"><path class="icon-fill" d="M3.5 1.5l2.5 0 1 3.5-1.6 1.2a8 8 0 0 0 4.4 4.4L11 9l3.5 1v2.5c0 1-1 2-2 2A11 11 0 0 1 1.5 3.5c0-1 1-2 2-2z"/></svg>
        555-014-2290
      </li>
      <li>
        <svg viewBox="0 0 16 16" aria-hidden="true"><path class="icon-line" stroke-width="1.6" d="M1 3h14v10H1z M1.5 3.5L8 9l6.5-5.5"/></svg>
        maren@larkspurtalent.example
      </li>
      <li>
        <svg viewBox="0 0 16 16" aria-hidden="true"><g class="icon-line" stroke-width="1.4"><circle cx="8" cy="8" r="6.5"/><ellipse cx="8" cy="8" rx="2.8" ry="6.5"/><path d="M1.5 8h13M2.5 4.8h11M2.5 11.2h11"/></g></svg>
        www.larkspurtalent.example
      </li>
    </ul>
  </section>

</main>
</body>
</html>
```